Tolvane Inc., a third party debt collection agency needs a Website

Tolvane needs a very basic website (3 basic pages) so that consumers can download forms, potential employees can get required EEO language and see potential jobs, and to show that they are a consumer friendly organization.

I've attached a list of requirements and wishes titled "Tolvane Website Specifications"

Target Market(s)

Consumers that need to repay their government loans; Tolvane will walk through the process to assist them.

Industry/Entity Type

Financial Service

Coding

Coded - Design and coding required

Number of Pages Required

1 page

Font styles to use
Sans Serif

Colors
0355a3

Requirements
Must have
• Tolvane Logo
• See document "Tolvane Website Specifications" for all requirements

```html
<!DOCTYPE html>
<html lang="en">
<head>
<meta charset="utf-8">
<title>Tolvane Inc.</title>
<link rel="stylesheet" href="https://fonts.googleapis.com/css2?family=Roboto+Condensed:wght@400;700&family=Roboto:wght@400;700&family=Open+Sans:wght@400;700&display=swap">
<style>
:root{
  --navy:#27276e;
  --red:#8b1a1a;
  --ink:#333;
  --muted:#666;
  --rule:#d8d8d8;
  --hero-dark:#2c3553;
  --hero-mid:#3c4a74;
  --table:#e9d8b4;
  --badge:#4f86c6;
  --badge-deep:#1c6a99;
}
*{box-sizing:border-box;margin:0;padding:0}
html,body{width:957px;height:1200px;overflow:hidden;background:#fff}
body{position:relative;font-family:"Open Sans",sans-serif;color:var(--ink)}
.top-rule{position:absolute;left:0;top:0;width:957px;height:4px;background:var(--navy)}
.site-header{position:absolute;left:0;top:0;width:957px;height:95px}
.brand{position:absolute;left:61px;top:36px;display:flex;align-items:center;gap:8px;font-family:"Roboto Condensed",sans-serif;font-weight:700;font-size:27px;color:var(--red)}
.brand-mark{width:14px;height:14px;background:var(--navy)}
.main-nav a{position:absolute;top:0;height:62px;line-height:60px;font-family:"Roboto",sans-serif;font-size:15px;color:var(--ink);text-decoration:none;letter-spacing:.3px}
.main-nav .is-active{left:365px;width:98px;text-align:center;background:var(--navy);color:#fff;border-radius:0 0 5px 5px}
.hero{position:absolute;left:0;top:95px;width:957px;height:458px;background:linear-gradient(135deg,var(--hero-dark),var(--hero-mid))}
.hero-photo{position:absolute;right:0;top:0;width:560px;height:458px;background:radial-gradient(ellipse at 62% 48%,var(--table) 0%,#b9b4b0 30%,rgba(60,74,116,0) 70%)}
.hero-title{position:absolute;left:64px;top:98px;font-family:"Roboto Condensed",sans-serif;font-weight:400;font-size:34px;line-height:50px;color:#fff;text-transform:uppercase}
.btn-apply{position:absolute;left:61px;top:274px;width:318px;height:49px;background:var(--red);color:#fff;font-family:"Roboto Condensed",sans-serif;font-size:19px;line-height:49px;text-align:center;border-radius:3px;text-decoration:none}
.welcome{position:absolute;left:0;top:606px;width:957px;text-align:center}
.welcome h1{font-family:"Roboto Condensed",sans-serif;font-weight:400;font-size:38px;color:var(--navy)}
.welcome h1 span{color:var(--red)}
.welcome p{width:720px;margin:14px auto 0;font-size:12.5px;line-height:20px;color:var(--muted)}
.credentials{position:absolute;left:0;top:779px;width:957px;height:183px}
.divider{position:absolute;left:479px;top:0;width:1px;height:183px;background:var(--rule)}
.cred .badge{position:absolute}
.cred-text{position:absolute;top:20px;width:258px;display:flex;flex-direction:column;gap:6px}
.cred h2{font-family:"Roboto",sans-serif;font-weight:400;font-size:18.5px;line-height:25px;color:var(--navy)}
.cred p{font-size:12.5px;line-height:20px;color:var(--muted)}
.cred-a .badge{left:90px;top:22px;width:63px;height:63px;background:var(--badge)}
.cred-a .cred-text{left:212px}
.cred-b .badge{left:527px;top:22px;width:80px;height:80px;border-radius:50%;background:var(--badge-deep)}
.cred-b .cred-text{left:645px}
.btn-advice{position:absolute;left:367px;top:1034px;width:223px;height:58px;background:var(--navy);color:#fff;font-family:"Roboto Condensed",sans-serif;font-size:24px;line-height:58px;text-align:center;border-radius:5px 5px 0 0;text-decoration:none}
.advice-shadow{position:absolute;left:250px;top:1092px;width:457px;height:20px;background:radial-gradient(ellipse at 50% 0,rgba(0,0,0,.1),rgba(0,0,0,0) 70%)}
.footer-nav{position:absolute;left:0;top:1120px;width:957px;text-align:center;font-size:13.5px}
.footer-nav a{color:var(--muted);text-decoration:none;margin:0 14px}
.copyright{position:absolute;left:0;top:1165px;width:957px;text-align:center;font-size:12px;color:var(--muted)}
.copyright strong{color:var(--red)}
</style>
</head>
<body>
<div class="top-rule"></div>
<header class="site-header">
  <div class="brand"><span class="brand-mark"></span>Tolvane, Inc.</div>
  <nav class="main-nav">
    <a class="is-active" href="#">HOME</a>
    <a href="#" style="left:502px">CONSUMER INFORMATION</a>
    <a href="#" style="left:723px">CAREER</a>
    <a href="#" style="left:829px">CONTACT</a>
  </nav>
</header>

<section class="hero">
  <div class="hero-photo" role="img" aria-label="Overhead photo of a business team meeting around a table with laptop and documents"></div>
  <h2 class="hero-title">Assist consumers in<br>resolving their<br>obligations</h2>
  <a class="btn-apply" href="#">EMPLOYMENT APPLICATION FORM</a>
</section>

<section class="welcome">
  <h1>WELCOME TO <span>TOLVANE INC.</span></h1>
  <p>Tolvane is a third party debt collection agency that is focused on the collection of higher education loans.&nbsp; Tolvane is compliant with all federal, state, and local laws and is committed to the professional and fair treatment of consumers.&nbsp; Our goal is to assist consumers in resolving their obligations in the manner that best meets their needs and to provide information necessary in order for consumers to make an informed decision.</p>
</section>

<section class="credentials">
  <div class="divider"></div>
  <div class="cred cred-a">
    <div class="badge" role="img" aria-label="Credline Alliance member badge"></div>
    <div class="cred-text">
      <h2>Member of Credline Alliance</h2>
      <p>Lorem Ipsum is simply dummy text of the printing and typesetting industry. Lorem Ipsum has been the industry's standard dummy text ever since the 1500.</p>
    </div>
  </div>
  <div class="cred cred-b">
    <div class="badge" role="img" aria-label="Fair Commerce Council accreditation badge"></div>
    <div class="cred-text">
      <h2>Accredited by the Fair<br>Commerce Council</h2>
      <p>Lorem Ipsum is simply dummy text of the printing and typesetting industry. Lorem Ipsum has been the industry's standard dummy text ever since the 1500.</p>
    </div>
  </div>
</section>

<a class="btn-advice" href="#">FREE ADVICE</a>
<div class="advice-shadow"></div>

<footer>
  <nav class="footer-nav">
    <a href="#">Home</a><a href="#">Consumer</a><a href="#">Career</a><a href="#">Discloser</a>
  </nav>
  <p class="copyright">© <strong>Tolvane Inc.</strong> - 2016. All Rights Reserved.</p>
</footer>
</body>
</html>
```